VORELT B2B portal design
Fantastic design work, top communication and fast design changes! Many thanks,Jarek & Lutz from VORELT
Zielgruppe
We are a B2B Cloud Services StartUp that creates B2B logistics & supply chain processes between customer and its suppliers.
Aufgabenstellung
We need a modern responsive able design, that should consider that we are NOT presenting goods or clothes or similar on the portal pages but we show mainly data grids, kpi dashboards, forms, and setting panels to our customer and their suppliers.
The design must be clean and straight not to distract people from the important information in these data grids, kpi dashboards, forms, and settings panels.
We need our logo perfectly embedded and the pages coloured around from grey to blue.
The Designer must be able to deliver a design and transfer it to a highly responsive HTML (5) template (without technical content or further functionality). This our programmers will implement afterwards in .Net.
We need in total 3 page templates:
1. Login Page
2. Main Page with overview over the following services text (each one shown in one tile)
"ZMS (Time Frame Management)"
"DMS (Document Management)"
"REMS (Reporting Management)"
-> Note: At the end we will have up to 12 or more tiles (services) so the design should be additive
3. Data grid (e.g. list of customers)/form (e.g. customer registration form) page to show some data grid with database data
See samples for each page enclosed!!

```html
<!DOCTYPE html>
<html lang="en">
<head>
<meta charset="utf-8">
<title>VORELT – User Registration</title>
<link href="https://fonts.googleapis.com/css2?family=Ubuntu:wght@400;500;700&display=swap" rel="stylesheet">
<style>
  :root {
    --navy: #0d2a45;
    --header-bg: #e2e7ea;
    --page-bg: #f5f7f9;
    --side-bg: #e2e7ea;
    --side-line: #cdd4d9;
    --card: #ffffff;
    --text: #2d3a45;
    --muted: #555f68;
    --placeholder: #a9b0b6;
    --field-line: #c4cacf;
    --focus-line: #3f7fae;
    --ok-bg: #e3f3d6;
    --ok-line: #8fcc6a;
    --ok-text: #3d8a1f;
    --err-bg: #f3ddd5;
    --err-line: #d4785f;
    --err-text: #a8361c;
    --link-red: #e0261f;
  }
  * { box-sizing: border-box; margin: 0; padding: 0; }
  html, body { width: 1200px; height: 948px; overflow: hidden; }
  body { position: relative; background: var(--page-bg); font-family: "Ubuntu", sans-serif; color: var(--text); }

  .topbar { position: absolute; left: 0; top: 0; width: 1200px; height: 138px; background: var(--header-bg); border-bottom: 1px solid #b9c2c9; }
  .brand { position: absolute; left: 20px; top: 48px; display: flex; align-items: center; gap: 12px; }
  .brand-dot { width: 30px; height: 30px; border-radius: 50%; background: var(--navy); }
  .brand-name { font-size: 40px; font-weight: 700; color: var(--navy); letter-spacing: 1px; }

  .account { position: absolute; right: 0; top: 34px; height: 70px; width: 300px; }
  .account-name { position: absolute; right: 110px; top: 14px; font-size: 20px; font-weight: 500; color: var(--navy); white-space: nowrap; }
  .account-role { position: absolute; right: 110px; top: 40px; font-size: 14px; color: var(--muted); white-space: nowrap; }
  .avatar { position: absolute; right: 35px; top: 0; width: 66px; height: 66px; border-radius: 50%; background: radial-gradient(circle at 50% 40%, #8d7f74, #4a4a4a); border: 2px solid #c8d0d6; }
  .caret { position: absolute; right: 10px; top: 30px; }

  .sidebar { position: absolute; left: 20px; top: 142px; width: 265px; height: 706px; background: var(--side-bg); list-style: none; }
  .nav-item { height: 61px; display: flex; align-items: center; padding-left: 20px; gap: 10px; font-size: 20px; color: var(--navy); border-bottom: 1px solid var(--side-line); position: relative; }
  .nav-item:last-child { border-bottom: none; }
  .nav-item.is-active { background: var(--navy); color: #fff; }
  .nav-icon { width: 28px; height: 28px; flex: none; }
  .nav-arrow { position: absolute; right: 28px; top: 23px; }

  .page-title { position: absolute; left: 304px; top: 186px; font-size: 23px; font-weight: 400; color: #3b4650; }
  .card { position: absolute; left: 305px; top: 240px; width: 870px; height: 604px; background: var(--card); border-bottom: 2px solid #d6dbdf; }
  .lead { position: absolute; left: 0; top: 46px; width: 100%; text-align: center; font-size: 17px; color: var(--text); }

  .alert { position: absolute; top: 109px; width: 365px; height: 42px; border: 1px solid; border-radius: 2px; font-size: 15px; padding-left: 14px; line-height: 40px; }
  .alert-success { left: 51px; background: var(--ok-bg); border-color: var(--ok-line); color: var(--ok-text); }
  .alert-error { left: 447px; background: var(--err-bg); border-color: var(--err-line); color: var(--err-text); }

  .field { position: absolute; width: 260px; }
  .field-label { display: block; font-size: 14px; color: var(--muted); margin-bottom: 10px; }
  .field-input { width: 260px; height: 42px; border: 1px solid var(--field-line); border-radius: 4px; font-size: 14px; padding-left: 14px; line-height: 40px; color: var(--text); }
  .field-input.is-focus { border-color: var(--focus-line); }
  .field-input.is-empty { color: var(--placeholder); }
  .field-input.is-secret { color: var(--placeholder); letter-spacing: 2px; font-size: 13px; }

  .check { position: absolute; left: 53px; display: flex; align-items: center; gap: 8px; font-size: 14px; color: var(--muted); }
  .check-box { width: 20px; height: 20px; border-radius: 50%; background: #e2e7ea; display: flex; align-items: center; justify-content: center; }
  .terms-link { color: var(--link-red); }

  .btn-register { position: absolute; left: 57px; top: 494px; width: 118px; height: 42px; background: var(--navy); color: #fff; font-size: 14px; border: none; border-radius: 2px; font-family: "Ubuntu", sans-serif; letter-spacing: .3px; }

  .footer { position: absolute; left: 0; top: 887px; width: 1200px; height: 61px; background: #fff; border-top: 1px solid #e6e9ec; font-size: 16px; color: #4a545c; }
  .copyright { position: absolute; left: 14px; top: 19px; }
  .footer-links { position: absolute; right: 24px; top: 19px; }
</style>
</head>
<body>
  <header class="topbar">
    <div class="brand"><span class="brand-dot"></span><span class="brand-name">VORELT</span></div>
    <div class="account">
      <span class="account-name">Mark Olsen</span>
      <span class="account-role">Gest User</span>
      <div class="avatar" role="img" aria-label="User profile photo"></div>
      <svg class="caret" width="10" height="8" viewBox="0 0 10 8"><path d="M0 0h10L5 7z" fill="#6b757d"/></svg>
    </div>
  </header>

  <ul class="sidebar">
    <li class="nav-item">
      <svg class="nav-icon" viewBox="0 0 28 28"><rect x="2" y="9" width="24" height="10" rx="5" fill="none" stroke="#0d2a45" stroke-width="2"/><path d="M7 12v4M11 12v4M15 12v4M19 12v4" stroke="#0d2a45" stroke-width="1.5"/></svg>
      My News
    </li>
    <li class="nav-item">
      <svg class="nav-icon" viewBox="0 0 28 28"><circle cx="11" cy="8" r="5" fill="#0d2a45"/><path d="M2 24c0-7 4-10 9-10s7 2 8 4v6z" fill="#0d2a45"/><circle cx="22" cy="21" r="4" fill="none" stroke="#0d2a45" stroke-width="2"/></svg>
      My User Settings
    </li>
    <li class="nav-item is-active">
      <svg class="nav-icon" viewBox="0 0 28 28"><circle cx="10" cy="10" r="6" fill="none" stroke="#fff" stroke-width="4" stroke-dasharray="3 2"/><circle cx="21" cy="20" r="4" fill="none" stroke="#fff" stroke-width="3" stroke-dasharray="2 1.5"/></svg>
      Company Settings
    </li>
    <li class="nav-item">
      <svg class="nav-icon" viewBox="0 0 28 28"><path d="M5 23L17 11" stroke="#0d2a45" stroke-width="3" stroke-linecap="round"/><path d="M5 5l18 18" stroke="#0d2a45" stroke-width="3" stroke-linecap="round"/><circle cx="19" cy="8" r="4" fill="none" stroke="#0d2a45" stroke-width="2.5"/></svg>
      Configuration
    </li>
    <li class="nav-item">
      <svg class="nav-icon" viewBox="0 0 28 28"><rect x="2" y="5" width="5" height="4" fill="#0d2a45"/><rect x="9" y="5" width="17" height="4" fill="#0d2a45"/><rect x="2" y="12" width="5" height="4" fill="#0d2a45"/><rect x="9" y="12" width="17" height="4" fill="#0d2a45"/><rect x="2" y="19" width="5" height="4" fill="#0d2a45"/><rect x="9" y="19" width="17" height="4" fill="#0d2a45"/></svg>
      Services
      <svg class="nav-arrow" width="8" height="12" viewBox="0 0 8 12"><path d="M1 1l5 5-5 5" stroke="#0d2a45" stroke-width="2" fill="none"/></svg>
    </li>
    <li class="nav-item">
      <svg class="nav-icon" viewBox="0 0 28 28"><ellipse cx="14" cy="12" rx="11" ry="8" fill="#0d2a45"/><path d="M6 17l-3 7 8-4z" fill="#0d2a45"/></svg>
      Communication
    </li>
    <li class="nav-item">
      <svg class="nav-icon" viewBox="0 0 28 28"><path d="M12 6H6v16h16v-6" stroke="#0d2a45" stroke-width="2.5" fill="none"/><path d="M13 15L22 6M16 5h7v7" stroke="#0d2a45" stroke-width="2.5" fill="none"/></svg>
      Logout
    </li>
  </ul>

  <h1 class="page-title">User Registration Form</h1>

  <main class="card">
    <p class="lead">Please type your account info here.</p>
    <div class="alert alert-success">Success messae</div>
    <div class="alert alert-error">Error messae</div>

    <div class="field" style="left:51px; top:194px;">
      <label class="field-label">Username:</label>
      <div class="field-input is-focus">John|</div>
    </div>
    <div class="field" style="left:411px; top:194px;">
      <label class="field-label">Password:</label>
      <div class="field-input is-secret">•••••••</div>
    </div>
    <div class="field" style="left:51px; top:306px;">
      <label class="field-label">Mail:</label>
      <div class="field-input is-empty">Type your mail here</div>
    </div>
    <div class="field" style="left:411px; top:306px;">
      <label class="field-label">Phone:</label>
      <div class="field-input is-empty">Type your phone here</div>
    </div>

    <div class="check" style="top:406px;">
      <span class="check-box"><svg width="10" height="8" viewBox="0 0 10 8"><path d="M1 3l4 4 4-6" stroke="#6b757d" stroke-width="1.4" fill="none"/></svg></span>
      I Agree with <span class="terms-link">Terms Of Use</span>
    </div>
    <div class="check" style="top:442px;">
      <span class="check-box"><svg width="10" height="8" viewBox="0 0 10 8"><path d="M1 3l4 4 4-6" stroke="#6b757d" stroke-width="1.4" fill="none"/></svg></span>
      Remember me
    </div>

    <button class="btn-register">REGISTER</button>
  </main>

  <footer class="footer">
    <span class="copyright">© 2016 VORELT. All rights reserved.</span>
    <span class="footer-links">Help &nbsp;/&nbsp; Disclaimer &nbsp;/&nbsp; Contact</span>
  </footer>
</body>
</html>
```